My Coffee beans packaging design

Our company named Harbor Bean,We are a new coffee Roasters in CHINA. We need a packaging design for our new coffee beans we roasted.We would like to see designs that use bright color. The final design should communicate the professional and modern sense.We want to catch customers eyes.We would like it is outstanding.It is a freestyle design project.We would like to see different styles.Thank you for reading our requirement.
Updates

Project Deadline Extended
Reason: Thank you for designing these for us,we want some more design.

Target Market(s)

All the people who love coffee

Industry/Entity Type

Coffee Shop

Font styles to use
Serif
Sans Serif
Decorative
Script

Requirements
Must have
• We do not have anything must haves.
Nice to have
• We do not have anything must haves
Should not have
• We do not have anything mustn't haves

```html
<!DOCTYPE html>
<html lang="en">
<head>
<meta charset="utf-8">
<title>Harbor Bean – Coffee Roasters Bag</title>
<link rel="stylesheet" href="https://fonts.googleapis.com/css2?family=Lobster&family=Arimo:wght@400;700&family=Playfair+Display:wght@700&display=swap">
<style>
  :root {
    --page: #e4e4e6;
    --cream: #f1ead9;
    --cream-light: #faf6ec;
    --brown-dark: #2e1a10;
    --brown: #4a2a19;
    --brown-mid: #7a4a2c;
    --gold: #c9a24a;
    --gold-light: #f0d98a;
    --gold-dark: #8c6a22;
    --red: #c8171c;
    --white: #ffffff;
    --ink: #3a2214;
  }
  * { box-sizing: border-box; margin: 0; padding: 0; }
  html, body { width: 831px; height: 1200px; overflow: hidden; }
  body { background: var(--page); position: relative; }

  .bag {
    position: absolute; left: 150px; top: 30px; width: 530px; height: 1140px;
    background: linear-gradient(90deg, var(--cream) 0%, var(--cream-light) 50%, var(--cream) 100%);
    overflow: hidden;
  }
  .bag__band-top, .bag__band-bottom {
    position: absolute; left: 0; width: 100%;
    background: linear-gradient(180deg, var(--gold-light), var(--gold) 50%, var(--gold-dark));
  }
  .bag__band-top { top: 0; height: 30px; }
  .bag__band-bottom { bottom: 0; height: 50px; }
  .bag__stripe {
    position: absolute; left: 0; width: 100%; bottom: 66px; height: 10px; background: var(--red);
  }
  .bag__cup { position: absolute; left: 0; top: 30px; }

  .brand {
    position: absolute; top: 120px; left: 90px; width: 220px; text-align: center;
    font-family: "Playfair Display", serif; font-weight: 700; font-size: 24px;
    color: var(--gold); letter-spacing: 1px;
  }
  .brand__dot {
    display: block; width: 40px; height: 40px; margin: 0 auto 8px;
    border-radius: 50%; background: var(--gold);
  }

  .title {
    position: absolute; left: 100px; top: 290px;
    font-family: "Lobster", cursive; font-weight: 400; font-size: 140px; line-height: 1;
    color: var(--gold-light);
  }
  .subtitle {
    position: absolute; left: 190px; top: 452px;
    font-family: "Lobster", cursive; font-size: 50px; line-height: 1; color: var(--white);
  }

  .beans {
    position: absolute; left: 60px; top: 650px; width: 190px; height: 56px;
    border-radius: 50%;
    background: radial-gradient(ellipse at center, var(--brown-mid), var(--brown-dark) 70%, transparent 72%);
  }

  .label {
    position: absolute; left: 0; top: 815px; width: 100%; text-align: center;
    font-family: "Arimo", sans-serif; color: var(--ink);
  }
  .label__badge {
    display: inline-block; background: var(--red); color: var(--white);
    font-weight: 700; font-size: 24px; padding: 2px 22px; border-radius: 6px;
    letter-spacing: 1px;
  }
  .label__name { font-weight: 700; font-size: 36px; line-height: 1.1; margin-top: 6px; }

  .net {
    position: absolute; left: 30px; top: 990px;
    font-family: "Arimo", sans-serif; font-size: 18px; color: var(--ink);
  }
</style>
</head>
<body>
  <main class="bag">
    <div class="bag__band-top"></div>

    <svg class="bag__cup" width="530" height="700" viewBox="0 0 530 700" role="img" aria-label="Top view of a cup of dark coffee on a dark brown panel">
      <defs>
        <radialGradient id="coffeeFill" cx="0.45" cy="0.45" r="0.6">
          <stop offset="0" stop-color="#7a4a2c"/>
          <stop offset="1" stop-color="#2e1a10"/>
        </radialGradient>
      </defs>
      <rect x="0" y="0" width="220" height="610" fill="#2e1a10"/>
      <circle cx="320" cy="300" r="335" fill="#2e1a10"/>
      <circle cx="320" cy="300" r="302" fill="#ffffff"/>
      <circle cx="320" cy="300" r="292" fill="url(#coffeeFill)"/>
    </svg>

    <div class="brand"><span class="brand__dot"></span>Harbor Bean</div>

    <h1 class="title">Coffee</h1>
    <p class="subtitle">Roasters</p>

    <div class="beans" role="img" aria-label="Roasted coffee beans"></div>

    <div class="label">
      <span class="label__badge">PREMIUM</span>
      <p class="label__name">Roasters<br>Coffee Beans</p>
    </div>

    <p class="net">Net W 200 gms.</p>

    <div class="bag__stripe"></div>
    <div class="bag__band-bottom"></div>
  </main>
</body>
</html>
```